Realtor branding business card

modern, simple and self branding. Broker office logo needs to be used but not emphasized. Looking to brand myself

Target Market(s)

buyers, sellers and investors

Industry/Entity Type

Realtor

Contact Information for Business Card

Sample of my current business card on file

Requirements
Must have
• my website - tobiasmerrowkl.com
• Realtor logo
• Fair housing logo
Nice to have
• Colors from office logo but not a must
Should not have
• Do not want headshot

```html
<!DOCTYPE html>
<html lang="en">
<head>
<meta charset="utf-8">
<title>Tobias Merrow – Realtor Business Card</title>
<link href="https://fonts.googleapis.com/css2?family=Lato:wght@400;900&family=Oswald:wght@500&display=swap" rel="stylesheet">
<style>
  :root {
    --page: #ecebe8;
    --navy: #2b2870;
    --navy-deep: #25225f;
    --red: #d42a2a;
    --ink-black: #262626;
    --white: #ffffff;
    --soft-white: #f2f2f6;
  }
  * { box-sizing: border-box; margin: 0; padding: 0; }
  html, body { width: 1200px; height: 1200px; overflow: hidden; }
  body {
    background: var(--page);
    font-family: "Lato", sans-serif;
    display: flex;
    flex-direction: column;
    align-items: center;
    justify-content: center;
    gap: 60px;
  }
  .card {
    width: 900px;
    height: 514px;
    box-shadow: 0 10px 30px rgba(0,0,0,0.15);
    position: relative;
    overflow: hidden;
  }
  /* Back side */
  .card-back {
    background: linear-gradient(135deg, #1f1f1f 0%, var(--ink-black) 55%, #3a3a3a 100%);
    display: flex;
    align-items: center;
    justify-content: center;
  }
  .brand-name {
    font-family: "Lato", sans-serif;
    font-weight: 900;
    font-size: 64px;
    line-height: 1.05;
    text-align: center;
  }
  .card-back .brand-name { color: var(--white); }

  /* Front side */
  .card-front { display: flex; }
  .front-brand {
    width: 48%;
    background: var(--white);
    display: flex;
    align-items: center;
    justify-content: center;
  }
  .card-front .brand-name { color: var(--navy); font-size: 48px; }
  .front-contact {
    width: 52%;
    background: linear-gradient(160deg, #3b3680 0%, var(--navy) 45%, var(--navy-deep) 100%);
    color: var(--soft-white);
    padding: 110px 30px 0 50px;
  }
  .agent-name {
    font-family: "Oswald", sans-serif;
    font-weight: 500;
    font-size: 34px;
    letter-spacing: 0.5px;
    color: var(--white);
    line-height: 1.1;
  }
  .agent-title { font-size: 24px; margin-bottom: 6px; }
  .contact-list { list-style: none; font-size: 22px; line-height: 1.45; }
  .contact-list li { display: flex; align-items: center; gap: 12px; white-space: nowrap; }
  .contact-list svg { width: 16px; height: 16px; flex: none; }
  .contact-label { margin-right: 8px; }
  .address { font-size: 22px; line-height: 1.4; margin-top: 2px; }
  .badges { display: flex; gap: 10px; margin-top: 22px; }
  .badge { width: 34px; height: 34px; background: var(--soft-white); }
  .badge-home { clip-path: polygon(50% 0, 100% 40%, 100% 100%, 0 100%, 0 40%); }
</style>
</head>
<body>
  <section class="card card-back" aria-label="Card back">
    <p class="brand-name">Brightpath<br>Realty Group</p>
  </section>

  <section class="card card-front" aria-label="Card front">
    <div class="front-brand">
      <p class="brand-name">Brightpath<br>Realty Group</p>
    </div>
    <div class="front-contact">
      <h1 class="agent-name">TOBIAS MERROW</h1>
      <p class="agent-title">Realtor</p>
      <ul class="contact-list">
        <li>
          <svg viewBox="0 0 16 16"><path fill="#d42a2a" d="M3 1l3 3-1.5 2a9 9 0 0 0 5.5 5.5L12 10l3 3-2 2C7 15 1 9 1 3z"/></svg>
          <span><span class="contact-label">Cell:</span>+407 - 555 - 0148</span>
        </li>
        <li>
          <svg viewBox="0 0 16 16"><path fill="#d42a2a" d="M1 6c2-3 12-3 14 0l-3 1.5-1-2H5l-1 2zM3 8h10l1 6H2z"/></svg>
          <span><span class="contact-label">Office:</span>+407 - 555 - 0192</span>
        </li>
        <li>
          <svg viewBox="0 0 16 16"><rect x="1" y="3" width="14" height="10" fill="#d42a2a"/><path d="M1 3l7 6 7-6" fill="none" stroke="#2b2870" stroke-width="1.3"/></svg>
          <span>tmerrow@tobiasmerrowkl.com</span>
        </li>
        <li>
          <svg viewBox="0 0 16 16"><g fill="none" stroke="#d42a2a" stroke-width="1.4"><circle cx="8" cy="8" r="6.5"/><ellipse cx="8" cy="8" rx="3" ry="6.5"/><path d="M1.5 8h13"/></g></svg>
          <span>www.tobiasmerrowkl.com</span>
        </li>
      </ul>
      <p class="address">480 Lakeview Crossing<br>Dr. Winter Park, FL 32789</p>
      <div class="badges">
        <span class="badge" role="img" aria-label="Realtor membership badge"></span>
        <span class="badge badge-home" role="img" aria-label="Fair housing badge"></span>
      </div>
    </div>
  </section>
</body>
</html>
```